TK Homes - Stone Dorf Design

Looking for a double sides design, 1 side for my realestate and the other for home building. ( TK Homes on 1 side, Stone Dorf card on the other Side
Side 1 - Marek Tove ~ Vox Realty logo and Company ( the Property quarter )
Marek Tove
Marek@Marektove.example
IG - Marek_Bzq_Realtor
FB - marekt
Cell - 5558130467
3847 61 St Nw

Side 2
Marek Tove
5558130467
IG - Stonedorf_Bzq
Stonedorfdev@mailbox.example

Target Market(s)

Home buyers/ sellers

Industry/Entity Type

Home builders - Realestate

Contact Information for Business Card

Above

Requirements
Must have
• Black OR White background - my information -

```html
<!DOCTYPE html>
<html lang="en">
<head>
<meta charset="utf-8">
<title>TK Homes · Stone Dorf Design — Business Cards</title>
<link href="https://fonts.googleapis.com/css2?family=Tinos:wght@400;700&display=swap" rel="stylesheet">
<style>
  :root{
    --backdrop:#141416;
    --card:#1e1e22;
    --emboss:#26262b;
    --emboss-edge:#2f2f35;
    --gold:#f3c233;
    --blue:#1677c9;
    --white:#ffffff;
    --serif:"Tinos", "Times New Roman", serif;
  }
  *{margin:0;padding:0;box-sizing:border-box}
  html,body{width:1200px;height:780px;overflow:hidden;background:var(--backdrop)}
  .sheet{position:relative;width:1200px;height:780px;display:flex;align-items:center;justify-content:center;gap:40px}
  .card{position:relative;width:560px;height:320px;background:var(--card);overflow:hidden;
    border-left:2px solid var(--gold);border-bottom:2px solid var(--gold);font-family:var(--serif);color:var(--white)}
  .name-tab{position:absolute;top:0;right:24px;width:20px;height:44px}
  .name-tab.white{background:var(--white)}
  .name-tab.gold{background:var(--gold)}
  .person{position:absolute;top:10px;right:54px;display:flex;align-items:flex-end;gap:8px}
  .person-name{font-size:30px;font-weight:700;line-height:1}
  .person-role{font-size:14px;font-weight:700;line-height:1;padding-bottom:2px}
  .person-name .first{color:var(--blue)}
  .person-name .last{color:var(--gold)}
  .brand{position:absolute;display:flex;align-items:center;gap:10px;font-weight:700;line-height:1}
  .brand-mark{width:14px;height:14px}
  .builder .brand{left:44px;top:110px;font-size:46px;color:var(--white)}
  .builder .brand-mark{background:var(--white)}
  .realty .brand{left:44px;top:90px;font-size:46px;color:var(--blue)}
  .realty .brand-mark{background:var(--blue);border-radius:50%}
  .emboss-word{position:absolute;font-weight:700;color:var(--emboss);line-height:1;white-space:nowrap;
    text-shadow:-1px -1px 0 var(--emboss-edge),2px 3px 4px #111114}
  .builder .emboss-word{right:-10px;top:40px;font-size:118px}
  .realty .emboss-word{right:-6px;top:60px;font-size:150px}
  .contact{position:absolute;list-style:none;font-size:15px;line-height:19px}
  .contact li{display:flex;align-items:center;gap:8px}
  .contact svg{width:13px;height:13px;flex:none}
  .builder .contact{left:44px;bottom:28px}
  .builder .contact svg{fill:var(--white)}
  .realty .address{position:absolute;left:60px;top:170px;font-size:16px}
  .realty .contact{left:60px;bottom:20px}
  .realty .contact svg{fill:var(--blue)}
  .dot{width:12px;height:12px;border-radius:50%;background:currentColor;flex:none}
  .builder .dot{color:var(--white)}
  .realty .dot{color:var(--blue)}
</style>
</head>
<body>
<main class="sheet">

  <section class="card builder" aria-label="Stone Dorf Design card">
    <span class="name-tab white"></span>
    <div class="person"><span class="person-name">Marek Tove</span><span class="person-role">Director</span></div>
    <div class="emboss-word" aria-hidden="true">Stone Dorf</div>
    <div class="brand"><span class="brand-mark"></span>Stone Dorf</div>
    <ul class="contact">
      <li><svg viewBox="0 0 16 16"><path d="M3 1l3 3-1.5 2a9 9 0 0 0 5.5 5.5L12 10l3 3-2 2C7 15 1 9 1 3z"/></svg>5558130467</li>
      <li><span class="dot"></span>Stonedorf_Bzq</li>
      <li><svg viewBox="0 0 16 16"><path d="M1 3h14v10H1zM2 4l6 5 6-5v1l-6 5-6-5z"/></svg>Stonedorfdev@mailbox.example</li>
    </ul>
  </section>

  <section class="card realty" aria-label="TK Homes card">
    <span class="name-tab gold"></span>
    <div class="person"><span class="person-name"><span class="first">Marek</span> <span class="last">Tove</span></span><span class="person-role">Director</span></div>
    <div class="emboss-word" aria-hidden="true">TK</div>
    <div class="brand"><span class="brand-mark"></span>TK Homes</div>
    <p class="address">3847 61 St Nw</p>
    <ul class="contact">
      <li><svg viewBox="0 0 16 16"><path d="M3 1l3 3-1.5 2a9 9 0 0 0 5.5 5.5L12 10l3 3-2 2C7 15 1 9 1 3z"/></svg>5558130467</li>
      <li><span class="dot"></span>marekt</li>
      <li><span class="dot"></span>Marek_Bzq_Realtor</li>
      <li><svg viewBox="0 0 16 16"><path d="M1 3h14v10H1zM2 4l6 5 6-5v1l-6 5-6-5z"/></svg>Marek@Marektove.example</li>
      <li><svg viewBox="0 0 16 16"><path d="M8 1a7 7 0 1 0 0 14A7 7 0 0 0 8 1zm0 1.5a5.5 5.5 0 0 1 0 11 5.5 5.5 0 0 1 0-11zM2.5 7.3h11v1.4h-11zM7.3 2h1.4v12H7.3z"/></svg>www.marektove.example</li>
    </ul>
  </section>

</main>
</body>
</html>
```